VIP Card Design Project

uZorvo is a premium sneaker store selling brand name sneakers like Volta, Rexa, Kembro and etc. ( www.uzorvoshop.com ) We need to design a VIP card to promote one of our discount program called "Uzorvo VIP Band 17", which offers 24% discount off all full-priced items. The idea is because we have a "Peakline Gym center" (peaklinegym.com) next door and we are trying to design a discount program for people going to the fitness center.
The design is for the front of the card. The back will be black and white with benefits information and member information.
The front design need to include our logo, "VIP", "Band 17" and our web address "Uzorvo.com" and Chatterly and quibbr logo.
It will be a plastic card in the size of 3.375x2.125 (bleed size 3.5x2.25)

```html
<!DOCTYPE html>
<html lang="en">
<head>
<meta charset="utf-8">
<title>Uzorvo VIP Band 17 Card</title>
<link href="https://fonts.googleapis.com/css2?family=Open+Sans:wght@400;600;700;800&family=Source+Sans+3:wght@400;600&family=Titan+One&display=swap" rel="stylesheet">
<style>
  :root {
    --stage: #6e4426;
    --card: #fbfbfb;
    --green: #3fae49;
    --green-dark: #2d8f36;
    --orange: #f39221;
    --red: #c8191f;
    --yellow: #ffe01a;
    --gold: #e9b32c;
    --ink: #1d1d1d;
    --grey: #b9b9b9;
  }
  * { margin: 0; padding: 0; box-sizing: border-box; }
  html, body { width: 1200px; height: 467px; overflow: hidden; }
  body { background: var(--stage); font-family: "Open Sans", Arial, sans-serif; position: relative; }

  .card {
    position: absolute; background: var(--card); border-radius: 20px; overflow: hidden;
    box-shadow: 0 6px 14px rgba(0,0,0,.35);
  }
  .card-front { left: 55px; top: 62px; width: 530px; height: 343px; }
  .card-back { left: 612px; top: 58px; width: 528px; height: 347px; }
  .card svg.backdrop { position: absolute; inset: 0; }

  .vip-label {
    position: absolute; left: 37px; top: 14px; font-family: "Titan One", sans-serif;
    font-size: 34px; line-height: 1.1; color: var(--yellow); letter-spacing: 1px;
    text-shadow: 0 0 2px #8a4a00, 1px 2px 2px rgba(0,0,0,.35);
  }
  .band-label {
    position: absolute; left: 422px; top: 12px; font-family: "Titan One", sans-serif;
    font-size: 27px; line-height: 1.1; color: var(--yellow); text-shadow: 1px 2px 2px rgba(0,0,0,.35);
  }
  .band-number {
    position: absolute; left: 430px; top: 36px; font-weight: 800; line-height: 1.1;
    font-size: 64px; color: #fff; text-shadow: 2px 3px 3px rgba(0,0,0,.45);
  }
  .brand-name {
    position: absolute; left: 40px; top: 102px; font-weight: 800; font-size: 62px;
    color: var(--green); letter-spacing: -1px; line-height: 1;
  }
  .brand-tagline {
    position: absolute; left: 42px; top: 178px; font-size: 19px; line-height: 1.2; color: var(--grey);
    letter-spacing: .5px;
  }
  .shoe-photo {
    position: absolute; width: 86px; height: 78px; border-radius: 14px; border: 2px solid #ddd;
  }
  .shoe-1 { left: 33px; top: 240px; background: linear-gradient(135deg, #c0332d, #3a3a3a); transform: rotate(-8deg); }
  .shoe-2 { left: 118px; top: 236px; background: linear-gradient(135deg, #e6e6e6, #8d8d8d); transform: rotate(-4deg); }
  .shoe-3 { left: 203px; top: 226px; background: linear-gradient(135deg, #f2d36b, #b5402d); transform: rotate(-6deg); }
  .leaf {
    position: absolute; width: 26px; height: 22px; border-radius: 50%;
    background: radial-gradient(circle, #f6a23b, #d96b14);
  }
  .leaf-top { left: 195px; top: 26px; }
  .leaf-bottom { left: 478px; top: 255px; }
  .leaf-back { left: 358px; top: 290px; }

  .discount-badge { position: absolute; left: 312px; top: 78px; width: 170px; height: 165px; }
  .discount-text {
    position: absolute; left: 340px; top: 118px; width: 128px; color: #fff;
    font-weight: 700; line-height: 1.1; text-align: center;
  }
  .discount-text .headline { color: var(--orange); font-size: 17px; font-weight: 800; }
  .discount-text .sub { font-size: 11px; font-weight: 600; }
  .discount-text .items { font-size: 15px; font-weight: 800; text-align: right; padding-right: 6px; }
  .discount-text .stars { color: var(--gold); font-size: 8px; letter-spacing: 1px; text-align: right; padding-right: 14px; }
  .discount-figure {
    position: absolute; left: 298px; top: 170px; font-weight: 800; font-size: 92px;
    color: var(--gold); line-height: 1; letter-spacing: -4px;
    text-shadow: 2px 3px 3px rgba(0,0,0,.4);
  }

  .social {
    position: absolute; left: 342px; top: 282px; display: flex; gap: 10px;
    font-size: 12px; font-weight: 700; color: var(--ink);
  }
  .social span { display: flex; align-items: center; gap: 4px; }
  .social i { display: block; width: 10px; height: 10px; background: #3b6fb6; border-radius: 2px; }
  .social span + span i { background: #3fb6e4; }
  .web-front {
    position: absolute; left: 290px; top: 312px; width: 200px; text-align: center;
    font-size: 15px; font-weight: 600; color: var(--ink);
  }

  .back-title {
    position: absolute; left: 48px; top: 32px; display: flex; align-items: baseline; gap: 8px;
    color: var(--green); font-weight: 800; line-height: 1;
  }
  .back-title .name { font-size: 30px; letter-spacing: -.5px; }
  .back-title .word { font-size: 20px; color: var(--green-dark); }
  .web-back { position: absolute; left: 338px; top: 30px; font-size: 14px; color: #666; letter-spacing: .3px; }
  .benefits {
    position: absolute; left: 48px; top: 80px; font-family: "Source Sans 3", Arial, sans-serif;
    font-size: 13px; color: var(--ink); line-height: 20px; white-space: nowrap;
  }
  .benefits ol { list-style: none; margin-top: 16px; }
  .benefits li { display: flex; gap: 8px; margin-bottom: 2px; }
  .benefits li b { font-weight: 400; width: 14px; flex: none; }
  .benefits .accent { color: var(--red); }
</style>
</head>
<body>

<section class="card card-front" aria-label="VIP card front">
  <svg class="backdrop" width="530" height="343" viewBox="0 0 530 343">
    <defs>
      <linearGradient id="frontBand" x1="0" y1="0" x2="1" y2="0">
        <stop offset="0" stop-color="#f59a23"/>
        <stop offset=".45" stop-color="#e0461e"/>
        <stop offset="1" stop-color="#b3121a"/>
      </linearGradient>
    </defs>
    <path d="M0 0 H530 V235 C490 205 440 150 350 118 C250 82 150 55 0 80 Z" fill="url(#frontBand)"/>
    <path d="M0 80 C150 55 250 82 350 118 C440 150 490 205 530 235" fill="none" stroke="#fff" stroke-width="10"/>
    <path d="M0 92 C150 66 250 92 350 128 C440 160 490 213 530 243" fill="none" stroke="#8cc63f" stroke-width="3"/>
    <path d="M0 54 C80 35 160 40 230 58" fill="none" stroke="#9ed04a" stroke-width="4"/>
  </svg>

  <div class="leaf leaf-top" role="img" aria-label="Autumn leaf ornament"></div>
  <div class="leaf leaf-bottom" role="img" aria-label="Autumn leaf ornament"></div>

  <div class="vip-label">VIP</div>
  <div class="band-label">BAND</div>
  <div class="band-number">17</div>

  <div class="brand-name">uZorvo</div>
  <div class="brand-tagline">PEAKLINE GYM CENTER</div>

  <div class="shoe-photo shoe-1" role="img" aria-label="Photo of a red and black sneaker"></div>
  <div class="shoe-photo shoe-2" role="img" aria-label="Photo of a white sneaker"></div>
  <div class="shoe-photo shoe-3" role="img" aria-label="Photo of a yellow and red sneaker"></div>

  <svg class="discount-badge" viewBox="0 0 175 170" aria-hidden="true">
    <defs>
      <radialGradient id="badgeFill" cx=".4" cy=".35" r=".7">
        <stop offset="0" stop-color="#4a4a4a"/>
        <stop offset="1" stop-color="#0e0e0e"/>
      </radialGradient>
    </defs>
    <polygon fill="url(#badgeFill)" stroke="#d7d7d7" stroke-width="2"
      points="87,5 97,18 112,9 117,25 134,22 133,39 150,41 143,56 158,64 146,76 157,89 142,96 149,112 132,114 133,131 116,128 111,145 97,137 87,151 77,137 63,145 58,128 41,131 42,114 25,112 32,96 17,89 28,76 16,64 31,56 24,41 41,39 40,22 57,25 62,9 77,18"/>
  </svg>
  <div class="discount-text">
    <div class="headline">DISCOUNT</div>
    <div class="sub">off all full-priced</div>
    <div class="items">ITEMS</div>
    <div class="stars">★★★★★</div>
  </div>
  <div class="discount-figure">24</div>

  <div class="social">
    <span><i></i>Chatterly</span>
    <span><i></i>quibbr</span>
  </div>
  <div class="web-front">www.uzorvoshop.com</div>
</section>

<section class="card card-back" aria-label="VIP card back">
  <svg class="backdrop" width="528" height="347" viewBox="0 0 528 347">
    <defs>
      <linearGradient id="backBar" x1="0" y1="0" x2="1" y2="0">
        <stop offset="0" stop-color="#7a0c10"/>
        <stop offset=".5" stop-color="#c8191f"/>
        <stop offset="1" stop-color="#f39221"/>
      </linearGradient>
      <linearGradient id="backWave" x1="0" y1="0" x2="1" y2="0">
        <stop offset="0" stop-color="#f59a23"/>
        <stop offset=".5" stop-color="#e0461e"/>
        <stop offset="1" stop-color="#b3121a"/>
      </linearGradient>
    </defs>
    <rect x="300" y="54" width="218" height="10" fill="url(#backBar)"/>
    <path d="M0 318 C130 304 260 306 380 312 C450 315 500 304 528 288 V347 H0 Z" fill="url(#backWave)"/>
    <path d="M0 312 C130 298 260 300 380 306 C450 309 500 298 528 282" fill="none" stroke="#8cc63f" stroke-width="3"/>
  </svg>
  <div class="leaf leaf-back" role="img" aria-label="Autumn leaf ornament"></div>

  <div class="back-title"><span class="name">UZORVO</span><span class="word">Benefits</span></div>
  <div class="web-back">www.UZORVOSHOP.com</div>

  <div class="benefits">
    <p>The UZORVO Member Program entitles Members to the following benefits:</p>
    <ol>
      <li><b>A.</b><span>20% OFF your entire first purchase after you sign up (Limited Time Offer)<br>Certain items are excluded from this offer. Please see stores for details.</span></li>
      <li><b>B.</b><span>10% OFF every purchase while being a member.<br>Certain items are excluded from this offer. Please see stores for details.</span></li>
      <li><b>C.</b><span>Additional <span class="accent">10% OFF</span> and <span class="accent">FREE SHIPPING</span> when an item is out of stock in store<br>but can be shipped to you from another location.</span></li>
      <li><b>D.</b><span>Eligible to purchase exclusive items offered to members only.<br>Purchasing of exclusive items is limited to 1 item per member per 30 days.<br>Please see stores for details.</span></li>
    </ol>
  </div>
</section>

</body>
</html>
```